New, modern business card for growing audiology practice

We need a new business card for our audiology practice. Our logo and website have recently changed (more modern) and we want our business cards to reflect this change.
We conduct hearing tests, perform earwax removals, and fit & dispense hearing aids to our patients. We are a family owned practice in which the owner is the one who works directly with the patient. I have attached logos in various formats to use, as well as two ideas I found on this website; as well as a scanned copy of our current logo. Good luck!

Industry/Entity Type

Business

Contact Information for Business Card

Company name: Tolvera Hearing Center
Provider name: Peter Wolstenby, Au.D. F/NSB
Phone number: (440) 683-5127
Address: 837 W. Lindell Ave. Marlow Falls, OH 44187
email: tolverahearing@postvane.com
website: tolverahearing.com

Colors
000000
aaaaaa
dbdbdb
cacaca
9bcb3c
afd23c
cadf82
b1b1b1

Requirements
Must have
• My card must include information in the "details" section. In the attached images, I found a few that I liked and I would like to model after - "brisky bouncin'" and "Sound Method Center".
• Must be horizontal.
• Must include logos provided. I uploaded them in various file formats and various ways.
• Must match logo font, if possible, if not, please get as close as you can.
Nice to have
• I really like the idea of having a color on one side with just the logo and company name and the contact information and provider name on the other side. I also really like the idea of having the main color dominating on the logo/company side with accent of that same color on the contact side of the card.
Should not have
• Must not be vertical.

```html
<!DOCTYPE html>
<html lang="en">
<head>
<meta charset="utf-8">
<title>Tolvera Hearing Center – Business Card</title>
<link href="https://fonts.googleapis.com/css2?family=Lato:wght@400&family=Exo+2:ital,wght@1,700&family=Roboto:wght@400&display=swap" rel="stylesheet">
<style>
  :root {
    --backdrop: #505050;
    --card: #1e1e1e;
    --card-edge: #262626;
    --white: #f2f2f2;
    --soft: #dbdbdb;
    --accent: #7cbf3c;
  }
  * { box-sizing: border-box; margin: 0; padding: 0; }
  html, body { width: 799px; height: 1200px; overflow: hidden; }
  body {
    background: var(--backdrop);
    font-family: "Lato", sans-serif;
    position: relative;
  }
  .card {
    position: absolute;
    left: 80px;
    width: 640px;
    height: 366px;
    background: var(--card);
    border: 1px solid var(--card-edge);
    border-radius: 4px;
    box-shadow: 0 10px 28px rgba(0,0,0,.45);
    overflow: hidden;
  }
  .card--front { top: 117px; }
  .card--back { top: 717px; }

  /* front */
  .brand {
    position: absolute;
    left: 46px;
    top: 132px;
    display: flex;
    align-items: center;
    gap: 16px;
  }
  .brand__dot {
    width: 26px; height: 26px;
    border-radius: 50%;
    background: var(--accent);
    flex: none;
  }
  .brand__name {
    font-family: "Lato", sans-serif;
    font-weight: 400;
    font-size: 38px;
    letter-spacing: 1px;
    color: var(--white);
    text-transform: uppercase;
    white-space: nowrap;
  }
  .site-url {
    position: absolute;
    left: 96px;
    top: 232px;
    font-family: "Roboto", sans-serif;
    font-size: 15px;
    letter-spacing: 6px;
    color: var(--white);
  }
  .site-url__domain { color: var(--accent); }

  /* back */
  .provider {
    position: absolute;
    left: 40px;
    top: 40px;
  }
  .provider__name {
    font-family: "Exo 2", sans-serif;
    font-style: italic;
    font-weight: 700;
    font-size: 22px;
    color: var(--accent);
  }
  .provider__role {
    font-family: "Roboto", sans-serif;
    font-size: 12px;
    color: var(--white);
    margin-top: 4px;
  }
  .contacts {
    position: absolute;
    left: 40px;
    top: 172px;
    list-style: none;
    font-family: "Roboto", sans-serif;
    font-size: 13.5px;
    line-height: 19px;
    color: var(--white);
  }
  .contacts li { display: flex; gap: 10px; align-items: flex-start; }
  .contacts svg { width: 12px; height: 12px; margin-top: 3px; flex: none; fill: var(--accent); }
  .contacts .gap { width: 12px; flex: none; }

  .brand--back {
    position: absolute;
    right: 52px;
    bottom: 56px;
    display: flex;
    align-items: center;
    gap: 16px;
  }
  .brand--back .brand__dot { width: 32px; height: 32px; }
  .brand__stack {
    font-family: "Lato", sans-serif;
    font-weight: 400;
    color: var(--white);
    text-transform: uppercase;
    line-height: 1;
  }
  .brand__stack .line-1 { font-size: 40px; letter-spacing: 1px; }
  .brand__stack .line-2 { font-size: 21px; letter-spacing: .5px; margin-top: 4px; }
</style>
</head>
<body>

<section class="card card--front">
  <div class="brand">
    <span class="brand__dot"></span>
    <span class="brand__name">Tolvera Hearing Center</span>
  </div>
  <p class="site-url">www.<span class="site-url__domain">tolverahearing</span>.com</p>
</section>

<section class="card card--back">
  <div class="provider">
    <h1 class="provider__name">Peter Wolstenby, Au.D. F/NSB</h1>
    <p class="provider__role">Owner - Audiologist</p>
  </div>

  <ul class="contacts">
    <li>
      <svg viewBox="0 0 12 12"><path d="M6 0a4 4 0 0 0-4 4c0 3 4 8 4 8s4-5 4-8a4 4 0 0 0-4-4zm0 5.6A1.6 1.6 0 1 1 6 2.4a1.6 1.6 0 0 1 0 3.2z"/></svg>
      <span>837 W. Lindell Ave.</span>
    </li>
    <li><span class="gap"></span><span>Marlow Falls, OH 44187</span></li>
    <li>
      <svg viewBox="0 0 12 12"><path d="M2.4 0.5 4.3 2.6 3.2 4.1c.7 1.5 1.9 2.7 3.4 3.4l1.5-1.1 2.1 1.9-1 2.2C4.9 10.3 1.7 7.1 0.5 1.5z"/></svg>
      <span>(440) 683-5127</span>
    </li>
    <li>
      <svg viewBox="0 0 12 12"><path d="M0 2h12v8H0zM1 3v.4l5 3.3 5-3.3V3zm0 1.6V9h10V4.6L6 7.9z"/></svg>
      <span>tolverahearing@postvane.com</span>
    </li>
    <li>
      <svg viewBox="0 0 12 12"><path d="M6 0a6 6 0 1 0 0 12A6 6 0 0 0 6 0zm4.9 5.5H8.6A9 9 0 0 0 7.8 1.4a5 5 0 0 1 3.1 4.1zM6 11c-.7-.8-1.4-2.3-1.6-4.5h3.2C7.4 8.7 6.7 10.2 6 11zM4.4 5.5C4.6 3.3 5.3 1.8 6 1c.7.8 1.4 2.3 1.6 4.5zM4.2 1.4a9 9 0 0 0-.8 4.1H1.1a5 5 0 0 1 3.1-4.1zM1.1 6.5h2.3a9 9 0 0 0 .8 4.1 5 5 0 0 1-3.1-4.1zm6.7 4.1a9 9 0 0 0 .8-4.1h2.3a5 5 0 0 1-3.1 4.1z"/></svg>
      <span>www.tolverahearing.com</span>
    </li>
  </ul>

  <div class="brand--back">
    <span class="brand__dot"></span>
    <div class="brand__stack">
      <div class="line-1">Tolvera</div>
      <div class="line-2">Hearing Center</div>
    </div>
  </div>
</section>

</body>
</html>
```